Business card design

I am open to ideas. I was thinking of a vertical design, turning the name 90 degrees and placing it on the left edge, then some clipped portion of the fabulous tree with contact info on the bottom -- special emphasis on Web address:WhimBeads.comFor All Your Beading Needs121 E. Cotati AveCotati, CA 94931(707) 664-8343

```html
<!DOCTYPE html>
<html lang="en">
<head>
<meta charset="utf-8">
<title>Fern &amp; Glass Co. — Business Card</title>
<link rel="stylesheet" href="https://fonts.googleapis.com/css2?family=Libre+Baskerville:wght@400;700&family=Lora:wght@400&display=swap">
<style>
  :root {
    --page-bg: #e9e6e2;
    --frost-top: #f7f8f9;
    --frost-bottom: #dde2e6;
    --ink: #111111;
    --card-black: #0b0b0b;
    --contact-text: #d7cdc3;
    --rose-gold-light: #f2d6cf;
    --rose-gold-dark: #b98a80;
    --icon-fill: #e6ddd4;
  }
  * { margin: 0; padding: 0; box-sizing: border-box; }
  html, body {
    width: 1200px;
    height: 970px;
    overflow: hidden;
    background: var(--page-bg);
  }
  .business-card {
    position: absolute;
    left: 80px;
    top: 189px;
    width: 1040px;
    height: 592px;
    border-radius: 30px;
    overflow: hidden;
    background: linear-gradient(160deg, var(--frost-top), var(--frost-bottom));
    box-shadow: 0 14px 36px rgba(0, 0, 0, 0.22);
  }
  .card-waves {
    position: absolute;
    inset: 0;
    width: 1040px;
    height: 592px;
  }
  .brand-name {
    position: absolute;
    left: 70px;
    top: 270px;
    width: 380px;
    text-align: center;
    font-family: "Libre Baskerville", serif;
    font-weight: 700;
    font-size: 32px;
    color: var(--ink);
  }
  .holder {
    position: absolute;
    right: 50px;
    top: 78px;
    text-align: right;
    font-family: "Libre Baskerville", serif;
    color: var(--ink);
  }
  .holder-name { font-size: 32px; font-weight: 700; line-height: 1.1; }
  .holder-title { font-size: 19px; font-weight: 400; margin-top: 4px; }
  .contact {
    position: absolute;
    right: 50px;
    top: 370px;
    text-align: right;
    font-family: "Lora", serif;
    color: var(--contact-text);
  }
  .contact-address { font-size: 24px; line-height: 34px; letter-spacing: 0.5px; }
  .contact-line {
    display: flex;
    justify-content: flex-end;
    align-items: center;
    gap: 12px;
    font-size: 24px;
    letter-spacing: 0.5px;
    height: 40px;
  }
  .contact-address + .contact-line { margin-top: 16px; }
  .contact-icon { width: 32px; height: 32px; flex: none; }
</style>
</head>
<body>
  <div class="business-card">
    <svg class="card-waves" viewBox="0 0 1040 592" xmlns="http://www.w3.org/2000/svg" aria-hidden="true">
      <defs>
        <linearGradient id="rainbow-sweep" x1="0" y1="0" x2="1" y2="0">
          <stop offset="0" stop-color="#4b2f8f"/>
          <stop offset="0.3" stop-color="#2f8a3c"/>
          <stop offset="0.6" stop-color="#e9b21d"/>
          <stop offset="1" stop-color="#d9331c"/>
        </linearGradient>
        <linearGradient id="rose-gold" x1="0" y1="0" x2="1" y2="0">
          <stop offset="0" stop-color="var(--rose-gold-dark)"/>
          <stop offset="0.5" stop-color="var(--rose-gold-light)"/>
          <stop offset="1" stop-color="var(--rose-gold-dark)"/>
        </linearGradient>
      </defs>
      <path class="rainbow-swoosh" fill="url(#rainbow-sweep)"
        d="M0,405 C180,445 350,425 492,330 C360,438 180,478 0,462 Z"/>
      <path class="black-band" fill="var(--card-black)"
        d="M0,478 C220,520 400,470 580,360 C740,262 880,250 1040,275 L1040,592 L0,592 Z"/>
      <path class="rose-gold-swoosh" fill="url(#rose-gold)"
        d="M90,528 C320,560 500,470 660,372 C800,288 900,256 1000,248 C880,268 790,310 670,390 C520,490 330,560 90,528 Z"/>
      <path class="black-top-swoosh" fill="var(--card-black)"
        d="M340,468 C560,330 780,228 985,232 C800,246 610,322 390,462 Z"/>
    </svg>

    <div class="brand-name">Fern &amp; Glass Co.</div>

    <div class="holder">
      <div class="holder-name">Nora Ellison</div>
      <div class="holder-title">Manager</div>
    </div>

    <div class="contact">
      <div class="contact-address">348 W. Brindle Ave<br>Larkfield, CA 94938</div>
      <div class="contact-line">
        <span>(707) 555-0192</span>
        <svg class="contact-icon" viewBox="0 0 32 32" aria-hidden="true">
          <circle cx="16" cy="16" r="16" fill="var(--icon-fill)"/>
          <path d="M11 8 L14 8 L15.5 12 L13.5 13.5 C14.5 16 16 17.5 18.5 18.5 L20 16.5 L24 18 L24 21 C24 22.5 22.5 24 21 24 C14 23.5 8.5 18 8 11 C8 9.5 9.5 8 11 8 Z" fill="var(--card-black)"/>
        </svg>
      </div>
      <div class="contact-line">
        <span>FernGlassco.com</span>
        <svg class="contact-icon" viewBox="0 0 32 32" aria-hidden="true">
          <circle cx="16" cy="16" r="16" fill="var(--icon-fill)"/>
          <g fill="none" stroke="var(--card-black)" stroke-width="1.6">
            <circle cx="16" cy="16" r="9"/>
            <ellipse cx="16" cy="16" rx="4" ry="9"/>
            <line x1="7" y1="16" x2="25" y2="16"/>
            <path d="M9 11.5 H23 M9 20.5 H23"/>
          </g>
        </svg>
      </div>
    </div>
  </div>
</body>
</html>
```